The Wardrobe Sage needs a pricing flyer

Single page flyer for The Wardrobe Sage.
The Wardrobe Sage is a lead generation service exclusively for the custom closet industry.
You design quality closets we provide quality leads!
Value Points:
Leads for closet companies are exclusive with a first right of refusal. Meaning, if the closet company cannot handle all of the leads we can provide, we will sell the excess to other closet companies. We will never sell the same lead to two different closet companies.
Benefits:
Flat rate and easy to budget
Cancel at anytime
Choose from 3 types of leads
Lower cost compared to overall cost per lead from other sources
More leads allows hiring more designers
More leads grow the companies revenue
Less time managing other advertising models
3 service options.
$250 each
- We send you the lead
- You and your team set the appointment
- Setting the appointment is up to you
2. $275 each
- We send you the lead
- We guarantee the appointment
- Return unset appointments for a replacement
3. $375 each
- We are your call center
- We generate the lead
- We set the appointment
Contact:
The Wardrobe Sage
704-555-0183
leads@TheWardrobeSage.com

```html
<!DOCTYPE html>
<html lang="en">
<head>
<meta charset="utf-8">
<title>The Wardrobe Sage – Pricing Flyer</title>
<link rel="stylesheet" href="https://fonts.googleapis.com/css2?family=Merriweather:wght@400;700;900&family=Poppins:wght@400;500;600&family=Great+Vibes&display=swap">
<style>
:root{
  --ink:#231b15;
  --brown:#a8692f;
  --brown-deep:#5a3416;
  --brown-text:#9b5a22;
  --gold:#c9a23c;
  --gold-light:#e2c262;
  --tan:#b97a42;
  --yellow:#f5c04a;
  --paper:#f8f7f5;
  --band:#e2e1df;
  --white:#ffffff;
}
*{box-sizing:border-box;margin:0;padding:0}
html,body{width:800px;height:1200px;overflow:hidden;background:var(--paper)}
.flyer{position:relative;width:800px;height:1200px;overflow:hidden;font-family:"Poppins",sans-serif;color:var(--ink);background:var(--paper)}

.header{position:absolute;left:0;top:0;width:800px;height:240px;
  background:linear-gradient(90deg,#1a1918 0%,#2b2825 45%,#3a342f 75%,#2a2623 100%)}
.brand{position:absolute;left:26px;top:132px;width:240px;text-align:center;
  font-family:"Merriweather",serif;font-weight:400;font-size:23px;color:var(--white)}
.tagline{position:absolute;left:313px;top:44px;font-family:"Great Vibes",cursive;font-size:27px;color:var(--brown)}
.headline{position:absolute;left:313px;top:92px;font-family:"Merriweather",serif;font-weight:900;
  font-size:37px;line-height:48px;color:var(--white);letter-spacing:.3px}

.benefits{position:absolute;left:0;top:240px;width:280px;height:960px;background:var(--brown)}
.benefits h2{position:absolute;left:48px;top:30px;font-family:"Merriweather",serif;font-weight:700;font-size:33px;color:var(--yellow)}
.benefit-list{position:absolute;left:44px;top:98px;list-style:none}
.benefit-list li{display:flex;align-items:center;height:64px;color:var(--white);font-size:13.5px;line-height:16.5px}
.benefit-icon{flex:none;width:44px;height:44px;margin-right:16px}
.chair-photo{position:absolute;left:0;top:550px;width:280px;height:410px;
  background:radial-gradient(ellipse at 45% 50%,#a9a59d 0%,#8a857c 45%,#6d6860 70%,var(--brown) 100%)}

.intro{position:absolute;left:312px;top:278px;width:440px;padding-left:14px;border-left:3px solid var(--brown-text);
  font-size:13px;line-height:16px;color:var(--ink)}
.services-title{position:absolute;left:309px;top:388px;font-family:"Merriweather",serif;font-weight:700;font-size:30px;color:var(--ink)}
.services-title span{color:var(--brown-text)}

.service{position:absolute;left:309px;width:480px;height:92px}
.service .band{position:absolute;left:40px;top:16px;width:400px;height:62px;background:var(--band);
  clip-path:polygon(0 0,92% 0,100% 50%,92% 100%,0 100%)}
.badge{position:absolute;left:0;top:0;width:92px;height:92px;border-radius:50%;color:var(--white);text-align:center;
  box-shadow:0 3px 6px rgba(0,0,0,.25)}
.badge .price{display:block;margin-top:18px;font-family:"Merriweather",serif;font-weight:700;font-size:30px;line-height:34px}
.badge .price sup{font-size:14px;vertical-align:top;line-height:22px}
.badge .each{display:block;font-size:13px;line-height:14px}
.badge--gold{background:radial-gradient(circle at 40% 35%,var(--gold-light),var(--gold) 70%)}
.badge--gold .each{color:#5a3a10}
.badge--dark{background:var(--brown-deep)}
.badge--dark .each{color:var(--yellow)}
.badge--tan{background:var(--tan)}
.badge--tan .each{color:#4a2a10}
.feature{position:absolute;width:92px;font-size:11.5px;line-height:13.5px;color:var(--ink);font-weight:500}
.feature svg{width:9px;height:9px;vertical-align:-1px;margin-right:3px}
.col-1{left:100px}.col-2{left:196px}.col-3{left:292px}

.photo{position:absolute;top:806px;width:222px;height:256px;border:3px solid var(--tan)}
.photo--office{left:309px;background:linear-gradient(160deg,#4d5970 0%,#3a4458 55%,#c9c4bc 100%)}
.photo--walkin{left:541px;background:linear-gradient(180deg,#3a2a20 0%,#e8e2d8 45%,#5b3420 100%)}

.contact{position:absolute;left:316px;top:1096px;font-family:"Merriweather",serif}
.mail{font-size:17px;color:var(--ink)}
.mail svg{width:13px;height:10px;margin:0 4px 0 12px;vertical-align:0}
.mail strong{font-weight:700}
.phone{font-size:25px;font-weight:700;letter-spacing:2px;color:var(--ink);margin-top:4px}
.phone svg{width:18px;height:18px;margin-right:8px;vertical-align:-2px}
</style>
</head>
<body>
<div class="flyer">

  <header class="header" role="img" aria-label="Dark photograph of a custom walk-in closet"></header>
  <div class="brand">The Wardrobe Sage</div>
  <p class="tagline">The Wardrobe Sage is a lead generation service</p>
  <h1 class="headline">Exclusively for the<br>Custom Closet Industry</h1>

  <aside class="benefits">
    <h2>Benefits</h2>
    <ul class="benefit-list">
      <li><svg class="benefit-icon" viewBox="0 0 44 44"><circle cx="22" cy="22" r="20" fill="none" stroke="#fff" stroke-width="2"/><circle cx="22" cy="22" r="16" fill="#5a3416"/><circle cx="22" cy="19" r="6" fill="#fff"/><path d="M13 28h13l5-3" stroke="#fff" stroke-width="2" fill="none"/></svg>Flat rate and easy<br>to budget</li>
      <li><svg class="benefit-icon" viewBox="0 0 44 44"><circle cx="22" cy="22" r="20" fill="none" stroke="#fff" stroke-width="2"/><circle cx="22" cy="22" r="16" fill="#5a3416"/><rect x="15" y="15" width="14" height="14" rx="2" fill="none" stroke="#fff" stroke-width="2"/><path d="M18 18l8 8M26 18l-8 8" stroke="#fff" stroke-width="2"/></svg>Cancel at<br>anytime</li>
      <li><svg class="benefit-icon" viewBox="0 0 44 44"><circle cx="22" cy="22" r="20" fill="none" stroke="#fff" stroke-width="2"/><circle cx="22" cy="22" r="16" fill="#5a3416"/><circle cx="17" cy="26" r="4" fill="#fff"/><circle cx="26" cy="17" r="3" fill="#fff"/><circle cx="27" cy="27" r="2.5" fill="#fff"/></svg>Choose from 3 types<br>of leads</li>
      <li><svg class="benefit-icon" viewBox="0 0 44 44"><circle cx="22" cy="22" r="20" fill="none" stroke="#fff" stroke-width="2"/><circle cx="22" cy="22" r="16" fill="#5a3416"/><circle cx="22" cy="18" r="6" fill="#fff"/><path d="M22 26v5M18 28l4 4 4-4" stroke="#fff" stroke-width="2" fill="none"/></svg>Lower cost compared<br>to overall cost per lead<br>from other sources</li>
      <li><svg class="benefit-icon" viewBox="0 0 44 44"><circle cx="22" cy="22" r="20" fill="none" stroke="#fff" stroke-width="2"/><circle cx="22" cy="22" r="16" fill="#5a3416"/><circle cx="20" cy="20" r="6" fill="none" stroke="#fff" stroke-width="2"/><path d="M24.5 24.5l5 5" stroke="#fff" stroke-width="2.5"/></svg>More leads allows hiring<br>more designers</li>
      <li><svg class="benefit-icon" viewBox="0 0 44 44"><circle cx="22" cy="22" r="20" fill="none" stroke="#fff" stroke-width="2"/><circle cx="22" cy="22" r="16" fill="#5a3416"/><path d="M15 30v-4M19 30v-7M23 30v-10M27 30v-13" stroke="#fff" stroke-width="2.5"/></svg>More leads grow the<br>companies revenue</li>
      <li><svg class="benefit-icon" viewBox="0 0 44 44"><circle cx="22" cy="22" r="20" fill="none" stroke="#fff" stroke-width="2"/><circle cx="22" cy="22" r="16" fill="#5a3416"/><path d="M16 14h12M16 30h12M17 14l10 16M27 14l-10 16" stroke="#fff" stroke-width="2"/></svg>Less time managing<br>other advertising models</li>
    </ul>
    <div class="chair-photo" role="img" aria-label="Photograph of an upholstered grey armchair"></div>
  </aside>

  <p class="intro">Leads for closet companies are exclusive with a first right of refusal. Meaning, if the closet company cannot handle all of the leads we can provide, we will sell the excess to other closet companies. We will never sell the same lead to two different closet companies.</p>

  <h2 class="services-title">Our 3 <span>Services</span></h2>

  <section class="service" style="top:428px">
    <div class="band"></div>
    <div class="badge badge--gold"><span class="price"><sup>$</sup>250</span><span class="each">Each</span></div>
    <p class="feature col-1" style="top:28px"><svg viewBox="0 0 10 10"><rect x=".5" y=".5" width="9" height="9" fill="none" stroke="#5a3416"/><path d="M2 5l2 2 4-5" stroke="#5a3416" fill="none" stroke-width="1.4"/></svg>We send<br>you the<br>lead</p>
    <p class="feature col-2" style="top:28px"><svg viewBox="0 0 10 10"><rect x=".5" y=".5" width="9" height="9" fill="none" stroke="#5a3416"/><path d="M2 5l2 2 4-5" stroke="#5a3416" fill="none" stroke-width="1.4"/></svg>You and your<br>team set the<br>appointment</p>
    <p class="feature col-3" style="top:28px"><svg viewBox="0 0 10 10"><rect x=".5" y=".5" width="9" height="9" fill="none" stroke="#5a3416"/><path d="M2 5l2 2 4-5" stroke="#5a3416" fill="none" stroke-width="1.4"/></svg>Setting the<br>appointment<br>is up to you</p>
  </section>

  <section class="service" style="top:550px">
    <div class="band"></div>
    <div class="badge badge--dark"><span class="price"><sup>$</sup>275</span><span class="each">Each</span></div>
    <p class="feature col-1" style="top:28px"><svg viewBox="0 0 10 10"><rect x=".5" y=".5" width="9" height="9" fill="none" stroke="#5a3416"/><path d="M2 5l2 2 4-5" stroke="#5a3416" fill="none" stroke-width="1.4"/></svg>We send<br>you the<br>lead</p>
    <p class="feature col-2" style="top:28px"><svg viewBox="0 0 10 10"><rect x=".5" y=".5" width="9" height="9" fill="none" stroke="#5a3416"/><path d="M2 5l2 2 4-5" stroke="#5a3416" fill="none" stroke-width="1.4"/></svg>We<br>guarantee the<br>appointment</p>
    <p class="feature col-3" style="top:21px"><svg viewBox="0 0 10 10"><rect x=".5" y=".5" width="9" height="9" fill="none" stroke="#5a3416"/><path d="M2 5l2 2 4-5" stroke="#5a3416" fill="none" stroke-width="1.4"/></svg>Return unset<br>appointments<br>for a<br>replacement</p>
  </section>

  <section class="service" style="top:670px">
    <div class="band"></div>
    <div class="badge badge--tan"><span class="price"><sup>$</sup>375</span><span class="each">Each</span></div>
    <p class="feature col-1" style="top:24px"><svg viewBox="0 0 10 10"><rect x=".5" y=".5" width="9" height="9" fill="none" stroke="#5a3416"/><path d="M2 5l2 2 4-5" stroke="#5a3416" fill="none" stroke-width="1.4"/></svg>We are<br>your call<br>center</p>
    <p class="feature col-2" style="top:24px"><svg viewBox="0 0 10 10"><rect x=".5" y=".5" width="9" height="9" fill="none" stroke="#5a3416"/><path d="M2 5l2 2 4-5" stroke="#5a3416" fill="none" stroke-width="1.4"/></svg>We generate<br>the lead</p>
    <p class="feature col-3" style="top:24px"><svg viewBox="0 0 10 10"><rect x=".5" y=".5" width="9" height="9" fill="none" stroke="#5a3416"/><path d="M2 5l2 2 4-5" stroke="#5a3416" fill="none" stroke-width="1.4"/></svg>We set the<br>appointment</p>
  </section>

  <div class="photo photo--office" role="img" aria-label="Photograph of a navy blue custom home office with built-in cabinets"></div>
  <div class="photo photo--walkin" role="img" aria-label="Photograph of a lit walk-in closet with a wooden island"></div>

  <footer class="contact">
    <p class="mail">Mail us at<svg viewBox="0 0 13 10"><rect width="13" height="10" fill="#5a3416"/><path d="M0 0l6.5 5.5L13 0" stroke="#fff" fill="none"/></svg><strong>leads@TheWardrobeSage.com</strong></p>
    <p class="phone"><svg viewBox="0 0 24 24"><path d="M6.6 10.8a15.1 15.1 0 0 0 6.6 6.6l2.2-2.2a1 1 0 0 1 1-.25 11.4 11.4 0 0 0 3.6.57 1 1 0 0 1 1 1V20a1 1 0 0 1-1 1A17 17 0 0 1 3 4a1 1 0 0 1 1-1h3.5a1 1 0 0 1 1 1c0 1.25.2 2.45.57 3.57a1 1 0 0 1-.25 1z" fill="#9b5a22"/></svg>704-555-0183</p>
  </footer>

</div>
</body>
</html>
```